TALMORK

The business want a professional looking business card. We have a scetch we will add but want the extra upgrade, and would like more suggestions for variations of our business cards.

```html
<!DOCTYPE html>
<html lang="en">
<head>
<meta charset="utf-8">
<title>TALMORK business card</title>
<link rel="stylesheet" href="https://fonts.googleapis.com/css2?family=Montserrat:wght@400;500;700&display=swap">
<style>
  :root {
    --backdrop: #1b1b1c;
    --card: #161616;
    --card-edge: #242424;
    --gold: #d4a93f;
    --gold-soft: #a07d2c;
    --ink-light: #f1f1f1;
    --emboss: #2c2c2d;
    --emboss-dot: #333335;
  }
  * { box-sizing: border-box; margin: 0; padding: 0; }
  html, body {
    width: 1200px; height: 801px; overflow: hidden;
    background: var(--backdrop);
    font-family: "Montserrat", sans-serif;
  }
  .stage {
    position: relative; width: 1200px; height: 801px;
    display: flex; align-items: center; justify-content: center; gap: 60px;
  }
  .card {
    position: relative; width: 525px; height: 300px;
    background: var(--card);
    border: 1px solid var(--card-edge);
    border-radius: 16px;
    box-shadow: 0 18px 40px rgba(0,0,0,.55);
    overflow: hidden;
  }
  /* front */
  .card-front { display: flex; align-items: center; }
  .brand-panel {
    width: 45%; height: 100%;
    display: flex; flex-direction: column; align-items: center; justify-content: center; gap: 16px;
  }
  .brand-mark {
    width: 54px; height: 54px; border-radius: 50%;
    background: var(--gold);
  }
  .brand-name {
    font-weight: 500; font-size: 26px; letter-spacing: 6px;
    color: var(--gold);
  }
  .divider {
    width: 1px; height: 170px;
    background: linear-gradient(var(--gold-soft), var(--gold), var(--gold-soft));
  }
  .contact-panel { padding-left: 28px; }
  .person-name { font-weight: 700; font-size: 19px; color: var(--gold); }
  .person-role { font-size: 14px; color: var(--ink-light); margin-top: 2px; }
  .contact-list { list-style: none; margin-top: 22px; }
  .contact-item {
    display: flex; align-items: center; gap: 10px;
    font-size: 13.5px; color: var(--ink-light); margin-bottom: 9px;
  }
  .contact-icon { width: 13px; height: 13px; flex: none; }
  /* back */
  .card-back {
    display: flex; flex-direction: column; align-items: center; justify-content: center; gap: 22px;
    background: linear-gradient(135deg, #1a1a1a 0%, #121212 60%, #181818 100%);
  }
  .card-back .brand-mark { width: 72px; height: 72px; background: var(--emboss-dot); }
  .card-back .brand-name { font-size: 38px; letter-spacing: 9px; color: var(--emboss); }
</style>
</head>
<body>
<main class="stage">
  <section class="card card-front" aria-label="Card front">
    <div class="brand-panel">
      <span class="brand-mark" aria-hidden="true"></span>
      <span class="brand-name">TALMORK</span>
    </div>
    <div class="divider" aria-hidden="true"></div>
    <div class="contact-panel">
      <h1 class="person-name">Aksel Brenna Lindvik</h1>
      <p class="person-role">CEO &amp; Founder</p>
      <ul class="contact-list">
        <li class="contact-item">
          <svg class="contact-icon" viewBox="0 0 24 24"><path fill="var(--gold)" d="M6.6 10.8a15.1 15.1 0 0 0 6.6 6.6l2.2-2.2a1 1 0 0 1 1-.25 11.4 11.4 0 0 0 3.6.57 1 1 0 0 1 1 1V20a1 1 0 0 1-1 1A17 17 0 0 1 3 4a1 1 0 0 1 1-1h3.5a1 1 0 0 1 1 1c0 1.25.2 2.45.57 3.57a1 1 0 0 1-.25 1z"/></svg>
          004790415276
        </li>
        <li class="contact-item">
          <svg class="contact-icon" viewBox="0 0 24 24"><path fill="var(--gold)" d="M2 5h20v14H2zm2 2v.5l8 5 8-5V7z"/></svg>
          post@talmork-mail.com
        </li>
        <li class="contact-item">
          <svg class="contact-icon" viewBox="0 0 24 24"><circle cx="12" cy="12" r="10" fill="none" stroke="var(--gold)" stroke-width="2"/><path d="M2 12h20M12 2c3 3 3 17 0 20M12 2c-3 3-3 17 0 20" fill="none" stroke="var(--gold)" stroke-width="1.6"/></svg>
          www.talmork.llc
        </li>
      </ul>
    </div>
  </section>
  <section class="card card-back" aria-label="Card back">
    <span class="brand-mark" aria-hidden="true"></span>
    <span class="brand-name">TALMORK</span>
  </section>
</main>
</body>
</html>
```